New career and executive coaching business needs a business card design including logo

Company name: 'Bramblefield Growth Partners.' The aim of my coaching engagements is to help people improve their communication in the workplace and achieve their career goals. The process involves working with individuals to help them uncover their strengths and talents, then leverage those to improve their working lives. The Tarwick Inventory is the starting point to the process. I am after an exciting and interesting business card design (including logo)which is professional yet will still get people's attention.

Industry/Entity Type

Business

Contact Information for Business Card

Name: Malcolm Dervaney
Position: Owner
Address: 58 Quorrin Ct, Elmbridge Vic 3190
Phone: 0418923047
Website: bramblefieldgrowth.com.au
Email: malcolm@bgp.com.au

Colors
33a6d7
00a990
0355a3
3176b5

Requirements
Must have
• logo

```html
<!DOCTYPE html>
<html lang="en">
<head>
<meta charset="utf-8">
<title>Bramblefield Growth Partners – Business Card</title>
<link href="https://fonts.googleapis.com/css2?family=Open+Sans:wght@400;600&display=swap" rel="stylesheet">
<style>
  :root {
    --teal: #00a990;
    --navy: #0355a3;
    --ink: #1a1a1a;
    --white: #ffffff;
    --backdrop: #e9ecee;
  }
  * { box-sizing: border-box; margin: 0; padding: 0; }
  html, body {
    width: 1200px; height: 900px; overflow: hidden;
    background: var(--backdrop);
    font-family: "Open Sans", Arial, sans-serif;
  }
  .canvas { position: relative; width: 1200px; height: 900px; }
  .card {
    position: absolute; width: 580px; height: 350px; overflow: hidden;
    box-shadow: 0 6px 18px rgba(0,0,0,.18);
  }
  .card-front { left: 80px; top: 40px; background: var(--white); }
  .card-back  { left: 385px; top: 508px; background: var(--teal); }
  .card-bands { position: absolute; inset: 0; }

  .brand {
    position: absolute; display: flex; align-items: center; gap: 12px;
    font-weight: 600; white-space: nowrap; letter-spacing: .2px;
  }
  .brand-mark { width: 22px; height: 22px; flex: none; }
  .card-front .brand { left: 0; right: 0; top: 66px; justify-content: center; font-size: 28px; color: var(--ink); }
  .card-front .brand-mark { background: var(--teal); }
  .card-back .brand { left: 0; right: 0; top: 156px; justify-content: center; font-size: 28px; color: var(--white); }
  .card-back .brand-mark { background: var(--white); }

  .contact-list {
    position: absolute; right: 292px; top: 230px; list-style: none;
    color: var(--white); font-size: 14.5px; line-height: 23px; text-align: right;
  }
  .contact-list li { display: flex; align-items: center; justify-content: flex-end; gap: 9px; }
  .contact-icon { width: 12px; height: 12px; flex: none; }

  .person { position: absolute; left: 323px; top: 214px; color: var(--white); }
  .person-name { font-size: 19px; font-weight: 600; line-height: 24px; }
  .person-role { font-size: 14.5px; line-height: 18px; }
  .person-address { font-size: 14.5px; line-height: 25px; margin-top: 17px; font-style: normal; }
</style>
</head>
<body>
<main class="canvas">

  <section class="card card-front" aria-label="Business card front">
    <svg class="card-bands" viewBox="0 0 580 350" width="580" height="350" aria-hidden="true">
      <polygon points="0,167 402,167 378,192 0,192" fill="var(--navy)"/>
      <polygon points="412,159 580,159 580,350 0,350 0,197 381,197" fill="var(--teal)"/>
    </svg>

    <div class="brand"><span class="brand-mark"></span>Bramblefield Growth Partners</div>

    <ul class="contact-list">
      <li>0418923047
        <svg class="contact-icon" viewBox="0 0 12 12"><path d="M2.5 1 L4.3 1 L5 3.5 L3.8 4.4 Q4.8 6.6 7.2 7.9 L8.1 6.8 L11 7.4 L11 9.3 Q10.8 11 9 11 Q1 10 1 2.6 Q1 1 2.5 1Z" fill="var(--white)"/></svg>
      </li>
      <li>malcolm@bgp.com.au
        <svg class="contact-icon" viewBox="0 0 12 12"><rect x="0.5" y="2" width="11" height="8" fill="var(--white)"/><path d="M0.8 2.4 L6 6.6 L11.2 2.4" stroke="var(--teal)" stroke-width="1" fill="none"/></svg>
      </li>
      <li>bramblefieldgrowth.com.au
        <svg class="contact-icon" viewBox="0 0 12 12"><circle cx="6" cy="6" r="5.5" fill="var(--white)"/><path d="M6 1 Q3 6 6 11 M6 1 Q9 6 6 11 M1 6 H11 M2 3.5 H10 M2 8.5 H10" stroke="var(--teal)" stroke-width=".8" fill="none"/></svg>
      </li>
    </ul>

    <div class="person">
      <p class="person-name">Malcolm Dervaney</p>
      <p class="person-role">Owner</p>
      <address class="person-address">58 Quorrin Ct,<br>Elmbridge Vic 3190</address>
    </div>
  </section>

  <section class="card card-back" aria-label="Business card back">
    <div class="brand"><span class="brand-mark"></span>Bramblefield Growth Partners</div>
  </section>

</main>
</body>
</html>
```